Business Card Design Project

I have established a company called "Corvella" which is a business specialising in psychotherapy/counselling , predominantly for anxiety & depression.

My name is Nel....hence, the Corvella link. However, Corvella was also chosen for its reference to green shoots of growth/recovery.

Corvella is to be "upmarket" and highly professional. I'm keen for the style and colours to reflect this.....taupe/grey with navy/black script, for example.....NO primary colours.

My name needs to be on the card and my mobile number. Not sure, but suspect it should also have my qualifications ( BA (Psych) & BSc (Hons) Psychology). Mobile number 0412 903 618.

```html
<!DOCTYPE html>
<html lang="en">
<head>
<meta charset="utf-8">
<title>Corvella – Business Card</title>
<link rel="stylesheet" href="https://fonts.googleapis.com/css2?family=Questrial&display=swap">
<style>
  :root {
    --backdrop: #e9e8ec;
    --charcoal: #4a4b4e;
    --paper: #f7f8f7;
    --leaf: #86a12a;
    --slate: #9a9b9e;
    --ink: #55565a;
    --ink-soft: #76777b;
  }
  * { margin: 0; padding: 0; box-sizing: border-box; }
  html, body {
    width: 1200px; height: 934px; overflow: hidden;
    background: var(--backdrop);
    font-family: "Questrial", "Helvetica Neue", Arial, sans-serif;
  }
  .sheet {
    position: relative; width: 1200px; height: 934px;
    display: flex; align-items: center; justify-content: center; gap: 44px;
  }
  .card {
    position: relative; width: 520px; height: 318px; overflow: hidden;
    box-shadow: 0 6px 18px rgba(60, 60, 70, 0.18);
  }
  /* Front */
  .card--front { background: var(--charcoal); }
  .front__accent-leaf {
    position: absolute; top: 0; left: 330px; width: 150px; height: 7px;
    background: var(--leaf);
  }
  .front__accent-slate {
    position: absolute; top: 7px; left: 400px; width: 120px; height: 18px;
    background: var(--slate);
  }
  .front__tab {
    position: absolute; left: 0; top: 176px; width: 10px; height: 34px;
    background: var(--slate);
  }
  .front__brand {
    position: absolute; left: 44px; top: 168px;
    font-size: 44px; letter-spacing: 2px; color: var(--leaf);
  }
  /* Back */
  .card--back { background: var(--paper); }
  .back__band {
    position: absolute; top: 0; left: 270px; width: 250px; height: 14px;
    background: #c4c5c7;
  }
  .back__band-slate {
    position: absolute; top: 14px; left: 230px; width: 290px; height: 14px;
    background: #a7a8ab;
  }
  .back__web {
    position: absolute; top: 40px; right: 22px;
    font-size: 13px; color: var(--ink-soft);
  }
  .back__web strong { color: var(--leaf); font-weight: 400; letter-spacing: 0.2px; }
  .back__name {
    position: absolute; left: 30px; top: 186px;
    font-size: 22px; letter-spacing: 0.5px; color: var(--ink);
  }
  .back__quals {
    position: absolute; left: 36px; top: 216px;
    font-size: 11.5px; color: var(--ink-soft);
  }
  .back__marker {
    position: absolute; left: 0; top: 258px; width: 16px; height: 28px;
    background: var(--leaf);
  }
  .back__contact {
    position: absolute; left: 34px; top: 252px; list-style: none;
    font-size: 13px; line-height: 19px; color: var(--ink-soft);
  }
  .back__contact .label { color: var(--leaf); font-weight: 700; display: inline-block; width: 16px; }
</style>
</head>
<body>
<main class="sheet">
  <section class="card card--front" aria-label="Card front">
    <div class="front__accent-leaf"></div>
    <div class="front__accent-slate"></div>
    <div class="front__tab"></div>
    <h1 class="front__brand">Corvella</h1>
  </section>

  <section class="card card--back" aria-label="Card back">
    <div class="back__band"></div>
    <div class="back__band-slate"></div>
    <p class="back__web">www.<strong>corvellaconsulting</strong>.com.au</p>
    <h2 class="back__name">NEL HARTLEY</h2>
    <p class="back__quals">BA (Psych) BSc (Hons) Psych MBPS</p>
    <div class="back__marker"></div>
    <ul class="back__contact">
      <li><span class="label">M</span> 0412 903 618</li>
      <li><span class="label">E</span> nel@corvellaconsulting.com.au</li>
    </ul>
  </section>
</main>
</body>
</html>
```